Pizza Coupon App Design Project

*******This project will have a guaranteed payout once I see that there is quality work being designed*********

I require the design (no coding) of 4 vertical screens (the screen will not change for horizontal orientation) for Zentrix and Orbalis. The highest res should be used so it can be scaled for older generation phones.

The mobile app will be used to access pizza coupons.

I do not have a specific style or look that I am going for, although I do not want a childish design (e.g. comic sans). The main requirements are for it to be very easy for users to understand and navigate and to be clean and professional.

I am happy if you only produce a design of the main and store selection screens to which I will give feedback before continuing to design the remaining screens.

The selected artist must be flexible in adapting the final design slightly after the contest is completed, during the app development process (maybe a few small modifications over a month or so).
Please do not include any copyrighted images in your deliverables. I must be the sole owner of the graphics once I have paid for them.

I have included attachments which show the process flow and the screen requirements so that will give you the detail you need to design them. I have also included the logo to assist you in your design., *******This project is now guaranteed *********

I have included attachments which show the process flow and the screen requirements so that will give you the detail you need to design them. I have also included the logo to assist you in your design., *******This project will have a guaranteed payout once I see that there is quality work being designed*********

I have included attachments which show the process flow and the screen requirements so that will give you the detail you need to design them. I have also included the logo to assist you in your design.

Reason: Still looking for the perfect design! ******Project is now guaranteed******

******Project is now guaranteed******

Reason: Starting to get some great designs, we are getting much closer! Keep it up.

Target Market(s)

students and 18-30 year olds - People who want cheap meals and people who order pizza online., students and 18-30 year olds - People who want cheap meals and people who order pizza online., students and 18-30 year olds - People who want cheap meals and people who order pizza online.

Industry/Entity Type

Store

Requirements
Must have
• Must have requirements are listed in the attached documents., Must have requirements are listed in the attached documents., Must have requirements are listed in the attached documents.

```html
<!DOCTYPE html>
<html lang="en">
<head>
<meta charset="utf-8">
<title>Select Your Store</title>
<link href="https://fonts.googleapis.com/css2?family=Roboto+Condensed:wght@700&family=Roboto:wght@400;700&display=swap" rel="stylesheet">
<style>
  :root{
    --page:#e9e4dc;
    --wood-dark:#3b2516;
    --wood-mid:#5a3a24;
    --wood-light:#6e4a2e;
    --bar-top:#ffd54a;
    --bar-bottom:#e8a10e;
    --bar-text:#4a3006;
    --search-bg:#2a1a10;
    --search-border:#1a0f08;
    --search-text:#e9ddd0;
    --card-top:#fffbe6;
    --card-bottom:#f3e6b0;
    --card-edge:#c9b06a;
    --accent:#e0231c;
    --name-rest:#8a7a5c;
    --detail:#3a2e1c;
    --pizza-a:#f2b640;
    --pizza-b:#c9762a;
    --status:#ffffff;
  }
  html,body{margin:0;padding:0;width:1200px;height:1040px;overflow:hidden;background:var(--page);}
  .canvas{position:relative;width:1200px;height:1040px;}
  .screen{
    position:absolute;left:320px;top:23px;width:320px;height:568px;
    transform:scale(1.75);transform-origin:0 0;overflow:hidden;
    font-family:"Roboto",Arial,sans-serif;
  }
  .wood{
    position:absolute;inset:0;
    background:linear-gradient(90deg,var(--wood-dark),var(--wood-mid) 30%,var(--wood-light) 55%,var(--wood-mid) 80%,var(--wood-dark));
  }
  .status-bar{
    position:absolute;left:0;top:0;width:320px;height:20px;background:rgba(0,0,0,.55);
    color:var(--status);font-size:11px;font-weight:700;display:flex;align-items:center;
  }
  .status-carrier{position:absolute;left:6px;display:flex;align-items:center;gap:3px;}
  .status-time{position:absolute;left:0;right:0;text-align:center;}
  .status-right{position:absolute;right:6px;display:flex;align-items:center;gap:4px;}
  .title-bar{
    position:absolute;left:10px;top:32px;width:300px;height:50px;border-radius:3px;
    background:linear-gradient(var(--bar-top),var(--bar-bottom));
    box-shadow:0 2px 3px rgba(0,0,0,.45);
  }
  .title-bar h1{
    margin:0;position:absolute;left:13px;top:14px;
    font:700 19px/22px "Roboto Condensed",Arial,sans-serif;color:var(--bar-text);
  }
  .search{
    position:absolute;left:10px;top:95px;width:300px;height:30px;border-radius:15px;
    background:var(--search-bg);border:1px solid var(--search-border);box-sizing:border-box;
    box-shadow:inset 0 1px 3px rgba(0,0,0,.6);
  }
  .search-icon{position:absolute;left:10px;top:8px;}
  .search-text{position:absolute;left:28px;top:7px;font-size:13px;color:var(--search-text);}
  .search-text::after{content:"";display:inline-block;width:1px;height:13px;background:var(--search-text);vertical-align:-2px;margin-left:1px;}
  .search-clear{position:absolute;right:6px;top:6px;}
  .store-list{position:absolute;left:10px;top:150px;width:300px;margin:0;padding:0;list-style:none;}
  .store-card{
    position:relative;height:69px;margin-bottom:10px;border-radius:3px;
    background:linear-gradient(var(--card-top),var(--card-bottom));
    border-bottom:1px solid var(--card-edge);box-shadow:0 1px 3px rgba(0,0,0,.5);
  }
  .store-photo{
    position:absolute;left:4px;top:10px;width:58px;height:46px;border-radius:4px;
    background:radial-gradient(circle at 45% 45%,var(--pizza-a),var(--pizza-b));
  }
  .store-name{position:absolute;left:96px;top:5px;margin:0;font-size:17px;font-weight:400;color:var(--name-rest);}
  .store-name .match{color:var(--accent);}
  .store-info{position:absolute;left:96px;top:28px;font-size:8px;line-height:12px;color:var(--detail);}
  .store-info b{font-weight:700;}
</style>
</head>
<body>
<div class="canvas">
  <div class="screen">
    <div class="wood" role="img" aria-label="Dark wooden plank background"></div>

    <div class="status-bar">
      <div class="status-carrier">
        <svg width="14" height="8" viewBox="0 0 14 8"><rect x="0" y="6" width="2" height="2" fill="#fff"/><rect x="3" y="4" width="2" height="4" fill="#fff"/><rect x="6" y="2" width="2" height="6" fill="#fff"/><rect x="9" y="0" width="2" height="8" fill="#fff"/></svg>
        <span>Vantel</span>
      </div>
      <div class="status-time">4:20 PM</div>
      <div class="status-right">
        <svg width="10" height="10" viewBox="0 0 10 10"><path d="M9 1 L1 5 L5 5 L5 9 Z" fill="#fff"/></svg>
        <svg width="22" height="10" viewBox="0 0 22 10"><rect x="0.5" y="0.5" width="18" height="9" rx="1.5" fill="none" stroke="#fff"/><rect x="2" y="2" width="15" height="6" fill="#fff"/><rect x="19.5" y="3" width="2" height="4" fill="#fff"/></svg>
      </div>
    </div>

    <header class="title-bar"><h1>Select Your Store</h1></header>

    <div class="search">
      <svg class="search-icon" width="12" height="12" viewBox="0 0 12 12"><circle cx="5" cy="5" r="3.6" fill="none" stroke="#e9ddd0" stroke-width="1.6"/><line x1="7.6" y1="7.6" x2="11" y2="11" stroke="#e9ddd0" stroke-width="1.8"/></svg>
      <span class="search-text">Pizza Pa</span>
      <svg class="search-clear" width="17" height="17" viewBox="0 0 17 17"><circle cx="8.5" cy="8.5" r="8" fill="#6b5a4c"/><path d="M5.5 5.5 L11.5 11.5 M11.5 5.5 L5.5 11.5" stroke="#2a1a10" stroke-width="1.8"/></svg>
    </div>

    <ul class="store-list">
      <li class="store-card">
        <div class="store-photo" role="img" aria-label="Pizza slices photo"></div>
        <h2 class="store-name"><span class="match">Pizza Pa</span>lace</h2>
        <div class="store-info">North Elm Road | Cedar Falls<br>WI 54012 | 555-018-2040<br><b>OPEN DAILY</b> 11am - 10pm</div>
      </li>
      <li class="store-card">
        <div class="store-photo" role="img" aria-label="Pizza slices photo"></div>
        <h2 class="store-name"><span class="match">Pizza</span> &amp; <span class="match">Pa</span>sta Corner</h2>
        <div class="store-info">42 Harbor Ave. | Bayview<br>NY 10090 | (555) 014-7721<br><b>OPEN DAILY</b> 11am - 10pm</div>
      </li>
      <li class="store-card">
        <div class="store-photo" role="img" aria-label="Pizza slices photo"></div>
        <h2 class="store-name"><span class="match">Pizza Pa</span>lace</h2>
        <div class="store-info">North Elm Road | Cedar Falls<br>WI 54012 | 555-018-2040<br><b>OPEN DAILY</b> 11am - 10pm</div>
      </li>
      <li class="store-card">
        <div class="store-photo" role="img" aria-label="Pizza slices photo"></div>
        <h2 class="store-name"><span class="match">Pizza</span> &amp; <span class="match">Pa</span>sta Corner</h2>
        <div class="store-info">42 Harbor Ave. | Bayview<br>NY 10090 | (555) 014-7721<br><b>OPEN DAILY</b> 11am - 10pm</div>
      </li>
      <li class="store-card">
        <div class="store-photo" role="img" aria-label="Pizza slices photo"></div>
        <h2 class="store-name"><span class="match">Pizza Pa</span>lace</h2>
        <div class="store-info">North Elm Road | Cedar Falls<br>WI 54012 | 555-018-2040<br><b>OPEN DAILY</b> 11am - 10pm</div>
      </li>
      <li class="store-card">
        <div class="store-photo" role="img" aria-label="Pizza slices photo"></div>
        <h2 class="store-name"><span class="match">Pizza</span> &amp; <span class="match">Pa</span>sta Corner</h2>
        <div class="store-info">42 Harbor Ave. | Bayview<br>NY 10090 | (555) 014-7721<br><b>OPEN DAILY</b> 11am - 10pm</div>
      </li>
    </ul>
  </div>
</div>
</body>
</html>
```